Retail Jewelry Business Card Design Project

We are in need of a new business card design for a retail jewelry store. This store is in the business of fine jewelry including but not specific to bridal jewelry, diamonds, designer jewelry and watches.

This store has been in business for 20 years but continues to strive for a modern professional appeal. The main colors use for this business are a royal blue, white and silver.

Target Market(s)

Target market is ages 18-50

Industry/Entity Type

Jewelry

Requirements
Must have
• Sales Person Name
Sales Person Email Address

Store Address
Store Phone
Website

Standard business card size. No odd shapes or sizes.
Nice to have
• Overall modern feel for card.

We have thought that a design with a nice feature of the logo on the back of the card would be nice but open to ideas.
Should not have
• No specific images of jewelry should be used.

```html
<!DOCTYPE html>
<html lang="en">
<head>
<meta charset="utf-8">
<title>Marlowe Grant Fine Jewelry – Business Card</title>
<link href="https://fonts.googleapis.com/css2?family=Tinos:wght@400;700&family=Kaushan+Script&display=swap" rel="stylesheet">
<style>
  :root {
    --royal: #2e3192;
    --lilac: #7b7bc0;
    --ink: #3f3f46;
    --paper: #ffffff;
    --backdrop: #eceef3;
  }
  * { box-sizing: border-box; margin: 0; padding: 0; }
  html, body {
    width: 1200px; height: 980px; overflow: hidden;
    background: var(--backdrop);
    font-family: "Tinos", "Times New Roman", serif;
  }
  .canvas { position: relative; width: 1200px; height: 980px; }

  .card {
    position: absolute;
    width: 620px; height: 354px;
    background: var(--paper);
    border-radius: 26px;
    overflow: hidden;
    box-shadow: 0 10px 30px rgba(40, 40, 70, 0.18);
  }
  .card--back { left: 500px; top: 80px; }
  .card--front { left: 80px; top: 530px; }

  .brand {
    position: absolute; left: 0; right: 0;
    text-align: center;
    color: var(--royal);
    font-weight: 700;
    line-height: 1;
  }
  .brand__name { display: block; font-size: 58px; letter-spacing: 0.5px; }
  .brand__tag { display: block; font-size: 24px; letter-spacing: 3px; margin-top: 10px; }

  .card--back .brand { top: 96px; }
  .website-line {
    position: absolute; left: 0; right: 0; top: 246px;
    text-align: center;
    font-size: 17px; letter-spacing: 4px;
    color: var(--ink);
  }

  .card--front .brand { top: 34px; }
  .card--front .brand__name { font-size: 48px; }
  .card--front .brand__tag { font-size: 20px; }

  .swoosh { position: absolute; inset: 0; width: 620px; height: 354px; }

  .contact {
    position: absolute; left: 150px; top: 140px;
    list-style: none;
    font-size: 16px; color: var(--ink);
  }
  .contact li { display: flex; align-items: center; gap: 8px; margin-bottom: 8px; }
  .contact svg { width: 14px; height: 14px; flex: none; }

  .person {
    position: absolute; left: 34px; bottom: 26px;
    font-family: "Kaushan Script", cursive;
    font-size: 24px;
    color: var(--paper);
  }
</style>
</head>
<body>
<main class="canvas">

  <section class="card card--back" aria-label="Card back">
    <h1 class="brand">
      <span class="brand__name">Marlowe Grant</span>
      <span class="brand__tag">FINE JEWELRY</span>
    </h1>
    <p class="website-line">www.marlowegrantjewelry.com</p>
  </section>

  <section class="card card--front" aria-label="Card front">
    <svg class="swoosh" viewBox="0 0 620 354" aria-hidden="true">
      <path d="M0,186 C110,268 300,330 600,354 L0,354 Z" fill="var(--royal)"/>
      <path d="M0,166 C120,256 300,318 560,352" fill="none" stroke="var(--lilac)" stroke-width="5"/>
    </svg>

    <h2 class="brand">
      <span class="brand__name">Marlowe Grant</span>
      <span class="brand__tag">FINE JEWELRY</span>
    </h2>

    <ul class="contact">
      <li>
        <svg viewBox="0 0 14 14" aria-hidden="true"><circle cx="7" cy="7" r="7" fill="var(--royal)"/><path d="M5 3.5 L6.5 5.5 L5.6 6.5 C6.2 7.7 6.8 8.3 8 8.9 L9 8 L11 9.5 L10 11 C6.5 10.5 3.6 7.5 3.4 4.4 Z" fill="#fff"/></svg>
        555-014-2736
      </li>
      <li>
        <svg viewBox="0 0 14 14" aria-hidden="true"><circle cx="7" cy="7" r="7" fill="var(--royal)"/><rect x="3" y="4.5" width="8" height="5.5" fill="#fff"/><path d="M3 4.5 L7 7.6 L11 4.5" fill="none" stroke="var(--royal)" stroke-width="0.9"/></svg>
        marlowe@marlowegrantjewelry.com
      </li>
      <li>
        <svg viewBox="0 0 14 14" aria-hidden="true"><circle cx="7" cy="7" r="7" fill="var(--royal)"/><circle cx="7" cy="7" r="4.2" fill="none" stroke="#fff" stroke-width="0.9"/><ellipse cx="7" cy="7" rx="1.8" ry="4.2" fill="none" stroke="#fff" stroke-width="0.9"/><path d="M2.8 7 H11.2" stroke="#fff" stroke-width="0.9"/></svg>
        www.marlowegrantjewelry.com
      </li>
      <li style="padding-left:22px">2208 Crescent Avenue, Bay Harbor, FL 32405</li>
    </ul>

    <p class="person">Marlowe Grant Hadley</p>
  </section>

</main>
</body>
</html>
```